Redesign a Start-Up Dating Website

Website: https://morvelique.com.
Make sure the design has an island style theme.
I would like the 7 pages of my website to have a new and professional look. I want the same colors to remain, but I want a creative look for all the pages. This is a dating website that is in the startup stage. So, I want to give my entire website a custom makeover. I want something that will stand out from the other dating sites. Something that will attract more people to want to use my services, and hopefully get new members.
Target Market(s)
Dating
Industry/Entity Type
Dating
Coding
Coded - Design and coding required
Number of Pages Required
5+ page
Font styles to use
Other font styles liked:
- Decorative, San Serif
Requirements
Must have
- The design must have the original colors and a stylish font to go along. The design must be creative, welcoming, and professional. I would like an island style theme for the website. This is a dating website so make sure that the design is tailored to that aspect.
Nice to have
- It would be nice to have a decorative font and a professional style on all the pages. Make sure the design will be mobile responsive and friendly for all the pages on the website.
Should not have
- The design should not be bland and uncreative.

```html
<!DOCTYPE html>
<html lang="en">
<head>
<meta charset="utf-8">
<title>Morvelique — Dating is easy</title>
<link href="https://fonts.googleapis.com/css2?family=Open+Sans:wght@300;400;600;700&display=swap" rel="stylesheet">
<style>
:root{
  --teal:#34b39a;
  --teal-soft:#66bba5;
  --teal-btn:#2fae96;
  --orange:#f08a1e;
  --purple:#6a3f9a;
  --ink:#2b2b2b;
  --muted:#666;
  --white:#fff;
}
*{box-sizing:border-box;margin:0;padding:0}
html,body{width:1200px;height:2761px;overflow:hidden}
body{font-family:"Open Sans",Arial,sans-serif;color:var(--ink);background:var(--white);position:relative}
.abs{position:absolute}
.center{text-align:center}

/* header */
.site-header{position:absolute;top:0;left:0;width:1200px;height:120px;background:var(--white)}
.brand{position:absolute;left:100px;top:36px;display:flex;align-items:center;gap:10px}
.brand-dot{width:50px;height:50px;border-radius:50%;background:var(--orange)}
.brand-name{font-size:34px;font-weight:700;color:var(--teal);white-space:nowrap}
.main-nav{position:absolute;left:414px;top:55px;width:486px;display:flex;justify-content:space-between;font-size:11.5px;font-weight:600;text-transform:uppercase;white-space:nowrap}
.main-nav a{color:var(--ink);text-decoration:none}
.main-nav a.active{color:var(--orange)}
.auth{position:absolute;right:100px;top:48px;display:flex;gap:10px}
.auth span{font-size:11px;font-weight:600;padding:6px 9px;border-radius:3px;display:flex;align-items:center;gap:5px;white-space:nowrap}
.login{border:1.5px solid var(--teal);color:var(--teal)}
.register{background:var(--teal);color:var(--white)}

/* hero */
.hero{top:120px;left:0;width:1200px;height:546px;background:linear-gradient(180deg,#8a7aa6 0%,#c9a3b8 30%,#b9a9c6 45%,#7f8fb1 58%,#4d5e85 68%,#6a5a7e 82%,#5a4a6c 100%)}
.hero-title{top:268px;left:0;width:1200px;font-size:54px;font-weight:700;color:var(--white);letter-spacing:1px;text-shadow:0 2px 4px rgba(0,0,0,.25);white-space:nowrap}
.hero-sub{top:338px;left:0;width:1200px;font-size:14px;font-weight:600;color:var(--white);text-transform:uppercase;white-space:nowrap}
.btn-orange{top:388px;left:506px;width:188px;height:46px;background:var(--orange);color:var(--white);font-size:19px;font-weight:600;display:flex;align-items:center;justify-content:center;border-radius:2px}
.dots{top:577px;left:558px;display:flex;gap:10px}
.dots i{width:15px;height:15px;border-radius:50%;background:var(--white);display:block}
.dots i:first-child{background:transparent;border:2px solid var(--white)}

/* quick search */
.quick-search{top:666px;left:0;width:1200px;height:222px;background:var(--teal-soft)}
.qs-title{top:40px;left:0;width:1200px;font-size:31px;font-weight:700;color:var(--white)}
.qs-field{top:105px}
.qs-field label{display:block;font-size:12px;color:var(--white);margin-bottom:10px}
.qs-select{height:40px;background:var(--white);font-size:11.5px;font-weight:600;padding:0 12px;display:flex;align-items:center;justify-content:space-between;color:var(--ink)}
.qs-btn{top:128px;left:957px;width:145px;height:44px;background:var(--teal-btn);color:var(--white);font-size:19px;font-weight:600;display:flex;align-items:center;justify-content:center}

/* welcome */
.welcome-title{top:940px;left:0;width:1200px;font-size:36px;font-weight:300;color:var(--ink)}
.welcome-text{top:1005px;left:200px;width:800px;font-size:13px;line-height:22px;color:var(--muted)}
.step{width:300px;text-align:center}
.step-icon{width:147px;height:147px;border-radius:50%;margin:0 auto;display:flex;align-items:center;justify-content:center;border:5px solid var(--white);box-shadow:0 0 0 4px currentColor}
.step h3{font-size:23px;font-weight:600;color:var(--ink);margin-top:26px}
.step p{font-size:13px;line-height:23px;color:var(--muted);margin:10px auto 0;width:280px}

/* story band */
.story{top:1475px;left:0;width:1200px;height:450px;background:linear-gradient(180deg,#f39a2c 0%,#ee8a1f 60%,#d9741a 100%)}
.story-art{top:0;left:400px;width:400px;height:450px;background:linear-gradient(180deg,rgba(160,80,10,0) 0%,rgba(170,85,15,.22) 40%,rgba(150,70,10,.3) 100%)}
.story-title{top:80px;left:0;width:1200px;font-size:40px;font-weight:300;color:var(--white)}
.story-text{top:150px;left:128px;width:944px;font-size:12px;line-height:24.5px;color:var(--white)}
.btn-outline{top:314px;left:507px;width:186px;height:46px;border:1.5px solid var(--white);color:var(--white);font-size:19px;font-weight:600;display:flex;align-items:center;justify-content:center}

/* members */
.members-title{top:1984px;left:0;width:1200px;font-size:36px;font-weight:300}
.member{top:2103px;width:200px;text-align:center}
.member-photo{width:162px;height:162px;border-radius:50%;margin:0 auto}
.member-name{font-size:13.5px;font-weight:700;color:var(--orange);margin-top:22px}
.member-place{font-size:13.5px;font-weight:600;color:var(--ink);margin-top:6px}

/* footer */
.site-footer{top:2418px;left:0;width:1200px;height:343px;background:var(--teal);color:var(--white)}
.f-head{font-size:18px;font-weight:600;text-transform:uppercase}
.f-links{font-size:14px;line-height:32px}
.f-contact{font-size:15px;line-height:29px;opacity:.95}
.f-contact .row{display:flex;align-items:center;gap:12px}
.news-form{display:flex;margin-top:16px}
.news-input{width:220px;height:38px;background:var(--white);font-size:13px;color:#aaa;padding:0 14px;display:flex;align-items:center}
.news-btn{width:105px;height:38px;background:var(--orange);font-size:13px;font-weight:600;display:flex;align-items:center;justify-content:center}
.socials{display:flex;gap:12px;margin-top:18px}
.socials i{width:37px;height:37px;border-radius:50%;background:var(--white);display:block}
.f-rule{top:272px;left:100px;width:1000px;height:1px;background:rgba(255,255,255,.45)}
.f-copy{top:290px;left:100px;font-size:13.5px}
</style>
</head>
<body>

<header class="site-header">
  <div class="brand"><span class="brand-dot"></span><span class="brand-name">Morvelique</span></div>
  <nav class="main-nav">
    <a class="active" href="https://morvelique.com">Home</a><a href="#">Search</a><a href="#">Members</a><a href="#">Extras</a><a href="#">About</a><a href="#">Premium</a><a href="#">Contact</a>
  </nav>
  <div class="auth">
    <span class="login"><svg width="10" height="11" viewBox="0 0 10 11"><circle cx="5" cy="3" r="2.6" fill="currentColor"/><path d="M0 11c0-3 2-4.5 5-4.5S10 8 10 11z" fill="currentColor"/></svg>LOGIN</span>
    <span class="register"><svg width="11" height="11" viewBox="0 0 11 11"><rect x="0.6" y="1.6" width="8" height="8.8" fill="none" stroke="currentColor" stroke-width="1.2"/><path d="M4 7l6-6" stroke="currentColor" stroke-width="1.6"/></svg>REGISTER</span>
  </div>
</header>

<section class="hero abs" role="img" aria-label="Couple walking hand in hand along a beach at sunset">
</section>
<h1 class="hero-title abs center">DATING IS EASY WITH MORVELIQUE</h1>
<p class="hero-sub abs center">Sign-up for a 30 days free trial enjoy all the benefits Morvelique has to offer with a full membership.</p>
<div class="btn-orange abs">JOIN UP FREE</div>
<div class="dots abs"><i></i><i></i><i></i><i></i></div>

<section class="quick-search abs">
  <h2 class="qs-title abs center">QUICK SEARCH</h2>
  <div class="qs-field abs" style="left:99px;width:180px"><label>I AM:</label><div class="qs-select">MAN<span>&#8964;</span></div></div>
  <div class="qs-field abs" style="left:304px;width:180px"><label>SEEKING A:</label><div class="qs-select">WOMAN<span>&#8964;</span></div></div>
  <div class="qs-field abs" style="left:510px;width:105px"><label>AGE:</label><div class="qs-select">18<span>&#8964;</span></div></div>
  <div class="qs-field abs" style="left:640px;width:105px"><label>TO:</label><div class="qs-select">99<span>&#8964;</span></div></div>
  <div class="qs-field abs" style="left:767px;width:155px"><label>COUNTRY:</label><div class="qs-select">INDIA<span>&#8964;</span></div></div>
  <div class="qs-btn abs">SEARCH</div>
</section>

<h2 class="welcome-title abs center">WELCOME TO MORVELIQUE</h2>
<p class="welcome-text abs center">Nemo enim ipsam voluptatem quia voluptas sit aspernatur aut odit aut fugit, sed quia consequuntur magni dolores eos qui ratione voluptatem sequi nesciunt</p>

<div class="step abs" style="left:95px;top:1104px">
  <div class="step-icon" style="background:var(--teal);color:var(--teal)">
    <svg width="60" height="60" viewBox="0 0 60 60"><circle cx="30" cy="20" r="12" fill="#fff"/><path d="M8 54c0-12 10-20 22-20s22 8 22 20z" fill="#fff"/></svg>
  </div>
  <h3>Create a Profile</h3>
  <p>Let people know all about you; the good and the quirky-show the world your true colors and find someone with the same unique qualities as you.</p>
</div>
<div class="step abs" style="left:450px;top:1104px">
  <div class="step-icon" style="background:var(--purple);color:var(--purple)">
    <svg width="60" height="56" viewBox="0 0 60 56"><path d="M30 54L6 30C-2 22 2 4 16 4c7 0 11 4 14 9 3-5 7-9 14-9 14 0 18 18 10 26z" fill="#fff"/></svg>
  </div>
  <h3>Find Matches</h3>
  <p>Browse other users and feel the excitement of getting your first message and getting to know potential dates in a safe and fun environment.</p>
</div>
<div class="step abs" style="left:805px;top:1104px">
  <div class="step-icon" style="background:var(--orange);color:var(--orange)">
    <svg width="56" height="64" viewBox="0 0 56 64"><g fill="#fff"><circle cx="15" cy="8" r="6"/><rect x="8" y="16" width="14" height="22" rx="3"/><rect x="9" y="36" width="5" height="26"/><rect x="16" y="36" width="5" height="26"/><circle cx="41" cy="8" r="6"/><path d="M35 16h12l6 26H29z"/><rect x="36" y="40" width="4" height="22"/><rect x="42" y="40" width="4" height="22"/></g></svg>
  </div>
  <h3>Start Dating</h3>
  <p>Once you've found your potential soulmate, it's time to meet up and say 'Hello' to the start of your journey together</p>
</div>

<section class="story abs">
  <div class="story-art abs" role="img" aria-label="Faint silhouette of a couple at sunset"></div>
  <h2 class="story-title abs center">Starts Dating Singles Today!</h2>
  <p class="story-text abs center">Morvelique aims to provide a straight-forward, easy-to-use online dating service. I won't over-complicate things or reduce the amount of people you can talk to with algorithms. I know that sometimes, opposites attract and sparks can fly with the last person you thought you'd be interested in-so I won't hide anybody from you.There is no discrimination on this dating site, it's not only about accepting young singles. I think everybody deserves love and should be given the same opportunity to find their true match. Especially when it comes to finding your perfect match, a broader community is always better. My trusted 24-hour service means that there are singles online at all times whether you're a night-owl or a morning person, there's always someone to connect with.</p>
  <div class="btn-outline abs">JOIN UP FREE</div>
</section>

<h2 class="members-title abs center">MORVELIQUE MEMBERS</h2>
<div class="member abs" style="left:80px"><div class="member-photo" role="img" aria-label="Member photo" style="background:radial-gradient(circle,#e8c98a,#c7902c)"></div><p class="member-name">Minima Veniam 28</p><p class="member-place">New York</p></div>
<div class="member abs" style="left:290px"><div class="member-photo" role="img" aria-label="Member photo" style="background:radial-gradient(circle,#cfc9c4,#6d5a4c)"></div><p class="member-name">Quis Nostrum 24</p><p class="member-place">Culpa Qui</p></div>
<div class="member abs" style="left:500px"><div class="member-photo" role="img" aria-label="Member photo" style="background:radial-gradient(circle,#c9b7a0,#6f5c4a)"></div><p class="member-name">Tempora Incidunt 23</p><p class="member-place">Officia Deserunt</p></div>
<div class="member abs" style="left:710px"><div class="member-photo" role="img" aria-label="Member photo" style="background:radial-gradient(circle,#7d8c90,#3f5058)"></div><p class="member-name">Rem Aperiam 27</p><p class="member-place">Est Laborum</p></div>
<div class="member abs" style="left:920px"><div class="member-photo" role="img" aria-label="Member photo" style="background:radial-gradient(circle,#d9d9d9,#5a5a5a)"></div><p class="member-name">Eaque Ipsa  21</p><p class="member-place">Mollit Anim</p></div>

<footer class="site-footer abs">
  <div class="abs" style="left:99px;top:44px">
    <p class="f-head">Quick Links</p>
    <div style="display:flex;gap:90px;margin-top:12px">
      <div class="f-links">Morvelique<br>About<br>Contact<br>Login<br>Members</div>
      <div class="f-links">Premium<br>Register<br>Search</div>
    </div>
  </div>
  <div class="abs" style="left:460px;top:44px;width:260px">
    <p class="f-head">Contact Info</p>
    <div class="f-contact" style="margin-top:12px">
      <p>Morvelique, Coral Bay, Palm Isles, 00417</p>
      <p class="row"><svg width="14" height="14" viewBox="0 0 14 14"><rect width="14" height="14" rx="2" fill="#fff"/><path d="M4 3l2 2-1 1.5c.6 1.2 1.3 1.9 2.5 2.5L9 8l2 2-1.5 1.5C6 11 3 8 2.5 4.5z" fill="var(--teal)"/></svg>(+01) 555-01472</p>
      <p class="row"><svg width="14" height="11" viewBox="0 0 14 11"><rect width="14" height="11" rx="1" fill="#fff"/><path d="M0 1l7 5 7-5" stroke="var(--teal)" stroke-width="1.3" fill="none"/></svg>contact@morvelique.com</p>
    </div>
  </div>
  <div class="abs" style="left:773px;top:44px;width:330px">
    <p class="f-head">Sign up for Newsletters</p>
    <p style="font-size:13.5px;margin-top:14px">Please sign up here for latest news</p>
    <div class="news-form"><div class="news-input">EMAIL ADDRESS</div><div class="news-btn">SUBSCRIBE</div></div>
    <div class="socials"><i></i><i></i><i></i><i></i></div>
  </div>
  <div class="f-rule abs"></div>
  <p class="f-copy abs">© 2017 MORVELIQUE.  All right reserved . Term of Use</p>
</footer>

</body>
</html>
```